VANTA Brouchure's

Project Overview:

We are seeking your expertise in designing a series of brochures for VANTA Systemworks. These brochures will be distributed to both current and prospective customers and need to effectively showcase our offerings in automation technology.

Requirements:

Image Utilization:

We have uploaded up to 40 images, which we have paid for and would like to see creatively arranged across different brochure designs.
The images should be utilized to emphasize key aspects of our business, including programming, design, robotics, PLC, and support.
Branding:

The VANTA Systemworks logo must be prominently displayed on both the front and back covers of each brochure for consistent branding.
Focus Areas:

Some brochures should specifically highlight our expertise in robotic solutions, particularly focusing on AGV and AMR technologies.
Additionally, our partnership with Morilendo and our capabilities in robotic arm technologies should be emphasized.
Contact Information:

Please include the following contact emails on each brochure: sales@vantasystemworks.example and admin@vantasystemworks.example.
We look forward to seeing your design concepts that align with our brand and effectively communicate our technological capabilities.

Also, please see attached a mock brochure, please use the wording for context.

```html
<!DOCTYPE html>
<html lang="en">
<head>
<meta charset="utf-8">
<title>VANTA Systemworks – Services Flyer</title>
<link href="https://fonts.googleapis.com/css2?family=Roboto:wght@300;400;500;700;900&display=swap" rel="stylesheet">
<style>
  :root{
    --stage:#e4e5ea;
    --blue-light:#2a93dc;
    --blue-mid:#1f84d3;
    --blue-deep:#1a78cc;
    --blue-royal:#1a5fc4;
    --ink:#1f1f24;
    --muted:#8a8d98;
    --white:#ffffff;
    --paper-top:#d9dbe6;
    --paper-bottom:#f6f6f9;
  }
  *{margin:0;padding:0;box-sizing:border-box}
  html,body{width:1200px;height:861px;overflow:hidden;background:var(--stage)}
  body{position:relative;font-family:'Roboto',sans-serif}
  .flyer-frame{position:absolute;left:325px;top:18px;width:550px;height:825px;overflow:hidden;box-shadow:0 6px 24px rgba(0,0,0,.18)}
  .flyer{position:absolute;left:0;top:0;width:869px;height:1303px;transform:scale(.633);transform-origin:0 0;background:linear-gradient(180deg,var(--paper-top),var(--paper-bottom))}
  .shapes{position:absolute;inset:0}
  .abs{position:absolute}
  .col-heading{color:var(--white);font-weight:500;font-size:25px;text-align:center;line-height:32px;letter-spacing:.2px}
  .col-heading::after{content:"";display:block;width:118px;height:3px;background:var(--white);margin:6px auto 0}
  .sub{color:var(--white);font-size:13.5px;font-weight:400;text-align:center}
  .list{color:var(--white);font-weight:300;font-size:14px;list-style:none}
  .list li{position:relative;padding-left:24px;line-height:35px}
  .list li::before{content:"·";position:absolute;left:0;font-weight:700}
  .prog{left:40px;top:440px;width:234px;color:var(--white);font-size:14px;font-weight:300}
  .prog .sub{line-height:35px}
  .prog .label{padding-left:38px;line-height:17.5px}
  .prog .item{padding-left:86px;line-height:17.5px;position:relative}
  .prog .item::before{content:"·";position:absolute;left:62px;font-weight:700}
  .contact{right:52px;top:720px;text-align:right;color:var(--ink);font-size:25px;font-weight:400;line-height:27.5px;font-style:normal}
  .industries-title{left:0;width:869px;top:864px;text-align:center;color:var(--blue-royal);font-weight:900;font-size:40px;letter-spacing:.3px}
  .industries{left:97px;top:923px;width:675px;height:210px;border:3px solid var(--ink);border-radius:18px;display:grid;grid-template-columns:1fr 1fr 1fr;grid-auto-rows:48.5px;padding-top:8px;align-items:center;text-align:center;font-size:19px;font-weight:500;color:var(--ink)}
  .tagline{left:0;width:869px;text-align:center}
  .tagline.upper{top:1148px;font-size:13px;font-weight:300;color:var(--muted);letter-spacing:.2px}
  .tagline.lower{top:1168px;font-size:14px;color:var(--ink)}
  .brand{left:47px;top:1218px;display:flex;align-items:center;gap:12px;height:70px}
  .brand-dot{width:46px;height:46px;border-radius:50%;background:var(--blue-royal)}
  .brand-name{font-size:44px;font-weight:900;color:var(--blue-royal);letter-spacing:1px}
  .website{left:264px;top:1237px;font-size:24px;line-height:30px;color:var(--ink)}
</style>
</head>
<body>
<div class="flyer-frame">
  <div class="flyer">
    <svg class="shapes" viewBox="0 0 869 1303" width="869" height="1303">
      <rect x="0" y="580" width="869" height="723" fill="#e3e4ed" opacity=".6" role="img" aria-label="Faded photograph of a control screen showing a process diagram"/>
      <polygon points="0,0 297,0 297,33 0,100" fill="var(--blue-light)"/>
      <polygon points="0,100 297,33 312,278 0,358" fill="#8f9096" role="img" aria-label="Photograph of a technician testing a control panel with a tablet"/>
      <polygon points="297,0 572,0 572,178 297,262" fill="#a9a7a3" role="img" aria-label="Photograph of wired terminal rails inside a control cabinet"/>
      <polygon points="572,0 869,0 869,78 572,153" fill="#9ea3ab" role="img" aria-label="Photograph of engineering workstation monitors with system drawings"/>
      <polygon points="0,358 314,278 314,818 0,860" fill="var(--blue-light)"/>
      <polygon points="314,262 584,178 584,718 314,790" fill="var(--blue-mid)"/>
      <polygon points="584,153 869,78 869,618 584,690" fill="var(--blue-deep)"/>
      <polygon points="555,1303 869,1193 869,1303" fill="var(--blue-royal)"/>
    </svg>

    <section class="abs" style="left:0;top:380px;width:314px">
      <h2 class="col-heading">PROGRAMMING</h2>
    </section>
    <div class="abs prog">
      <div class="sub">TORVANEL</div>
      <div class="label">Hardware:</div>
      <div class="item">Drivara Drives</div>
      <div class="item">Velnora Logic</div>
      <div class="item">Minvora Logic</div>
      <div class="label">Software:</div>
      <div class="item">Studio 900</div>
      <div class="item">Lumeric View</div>
      <div class="sub" style="margin-top:5px">ORVANTIC AUTOMATION</div>
      <div class="label">Software</div>
      <div class="item">Kestrune HMI</div>
      <div class="sub" style="margin-top:8px">HALVORNE, OBRISANT</div>
      <div class="sub">IO/MOTOR Checksheets</div>
      <div class="sub">Alarm Reports</div>
    </div>

    <section class="abs" style="left:304px;top:272px;width:274px">
      <h2 class="col-heading">DESIGN</h2>
      <div class="sub" style="margin-top:22px">SKETVORA</div>
      <ul class="list" style="margin-left:44px;margin-top:4px">
        <li>Cloud-based Program</li>
        <li>Smart PDFs</li>
      </ul>
    </section>

    <section class="abs" style="left:310px;top:500px;width:274px">
      <h2 class="col-heading">PROJECT<br>MANAGEMENT</h2>
      <ul class="list" style="margin-left:48px;margin-top:34px">
        <li>Custom Dashboards</li>
        <li>Digital Service Reports</li>
      </ul>
    </section>

    <section class="abs" style="left:584px;top:174px;width:285px">
      <h2 class="col-heading" style="margin-left:-14px">FABRICATION</h2>
      <ul class="list" style="margin-left:58px;margin-top:5px">
        <li>Automated Tooling</li>
        <li>Custom Panel Fabrication</li>
        <li>High-Quality Materials</li>
        <li>Maintenance Support</li>
        <li>Expert Craftsmanship</li>
      </ul>
    </section>

    <section class="abs" style="left:584px;top:400px;width:285px">
      <h2 class="col-heading" style="margin-left:-12px">SAFEY &amp;<br>COMPLIANCE</h2>
      <ul class="list" style="margin-left:63px;margin-top:38px">
        <li style="line-height:17.5px">Precommissioning<br>Checks</li>
        <li style="line-height:17.5px;margin-top:17px">Functional Safety<br>Checks</li>
      </ul>
    </section>

    <address class="abs contact">
      120 Halden Rd<br>
      555-014-2270<br>
      sales@vantasystemworks.example<br>
      admin@vantasystemworks.example
    </address>

    <h2 class="abs industries-title">INDUSTRIES SERVED</h2>
    <div class="abs industries">
      <span>Wood Processing</span><span>Asphalt Production</span><span>Automotive</span>
      <span>Steel</span><span>Pulp &amp; Paper</span><span>Biomass</span>
      <span>Food &amp; Beverage</span><span>Packaging</span><span>Agriculture</span>
      <span>Recycling</span><span>Textiles</span><span>&amp; More</span>
    </div>

    <p class="abs tagline upper">LEADING-EDGE AUTOMATION SERVICES IN SOUTHEASTERN ALABAMA FOR ALL MANUFACTUERERS</p>
    <p class="abs tagline lower">Setting the standard for process engineering and automation services since 1997</p>

    <div class="abs brand">
      <span class="brand-dot"></span>
      <span class="brand-name">VANTA</span>
    </div>
    <p class="abs website">vantasystemworks.example</p>
  </div>
</div>
</body>
</html>
```